Tolbek cards

I want a simple business card that pops.
Logo on one side.
On side two i want.
"Are you thinking about a new building on your property, or renovating an existing structure? Contact".....
Owners Name: Dale Whitacre
Owners Phone number: 610-555-0187
Address:4076 Copper Ridge RD, Larkfield, OH 43990
Committed to Quality, Service, and Integrity

```html
<!DOCTYPE html>
<html lang="en">
<head>
<meta charset="utf-8">
<title>Tolbek Builders LLC – Business Cards</title>
<link rel="stylesheet" href="https://fonts.googleapis.com/css2?family=Oswald:wght@700&family=Playfair+Display:ital,wght@1,600&family=Poppins:wght@300;400;600;700&display=swap">
<style>
  :root {
    --brown: #3f2b1c;
    --brown-light: #6b573f;
    --white: #ffffff;
    --backdrop: #2e2e2e;
    --rule: rgba(255,255,255,0.7);
  }
  * { margin: 0; padding: 0; box-sizing: border-box; }
  html, body {
    width: 1200px; height: 866px; overflow: hidden;
    background: var(--backdrop);
  }
  .sheet {
    width: 1200px; height: 866px;
    display: flex; flex-direction: column; align-items: center; justify-content: center;
    gap: 36px;
  }
  .card {
    width: 660px; height: 377px; position: relative; overflow: hidden;
    box-shadow: 0 12px 28px rgba(0,0,0,0.45);
  }

  /* Front */
  .card-front {
    background: linear-gradient(120deg, var(--brown) 0%, var(--brown) 55%, var(--brown-light) 100%);
    display: flex; align-items: center; justify-content: center;
  }
  .brand { display: flex; align-items: center; gap: 22px; }
  .brand-square { width: 58px; height: 58px; background: var(--white); flex: none; }
  .brand-name {
    font-family: "Poppins", sans-serif; font-weight: 700; font-size: 50px;
    color: var(--white); letter-spacing: 1px; line-height: 1; white-space: nowrap;
  }

  /* Back */
  .card-back { background: var(--white); }
  .pitch { position: absolute; left: 44px; top: 26px; width: 440px; color: var(--brown); }
  .pitch-lead {
    font-family: "Playfair Display", serif; font-style: italic; font-weight: 600;
    font-size: 26px; line-height: 1.1;
  }
  .pitch-question {
    font-family: "Oswald", sans-serif; font-weight: 700; text-transform: uppercase;
    font-size: 34px; line-height: 1.05; margin-top: 4px;
  }
  .contact-band {
    position: absolute; left: 0; right: 0; bottom: 0; height: 150px;
    background: var(--brown); color: var(--white);
    padding: 16px 44px 0 44px;
  }
  .contact-row { display: flex; justify-content: space-between; align-items: flex-end; }
  .contact-label { font-family: "Poppins", sans-serif; font-weight: 300; font-size: 15px; }
  .contact-name {
    font-family: "Poppins", sans-serif; font-weight: 600; font-size: 22px;
    text-transform: uppercase; letter-spacing: 1px; line-height: 1.15;
  }
  .contact-line {
    display: flex; align-items: center; gap: 8px;
    font-family: "Poppins", sans-serif; font-weight: 300; font-size: 16px;
  }
  .contact-line svg { flex: none; }
  .address { font-family: "Poppins", sans-serif; font-weight: 300; font-size: 15px; line-height: 1.3; }
  .address-block { display: flex; gap: 8px; align-items: flex-start; }
  .address-block svg { flex: none; margin-top: 1px; }
  .divider { height: 1px; background: var(--rule); margin: 10px 0 8px; }
  .tagline {
    font-family: "Poppins", sans-serif; font-weight: 700; font-size: 15px;
    text-transform: uppercase; letter-spacing: 1.2px; white-space: nowrap;
  }
</style>
</head>
<body>
<main class="sheet">
  <section class="card card-front" aria-label="Card front">
    <div class="brand">
      <span class="brand-square" aria-hidden="true"></span>
      <span class="brand-name">Tolbek Builders LLC</span>
    </div>
  </section>

  <section class="card card-back" aria-label="Card back">
    <div class="pitch">
      <p class="pitch-lead">Are you thinking about</p>
      <p class="pitch-question">A new building on your<br>property, or renovating<br>an existing structure?</p>
    </div>
    <div class="contact-band">
      <div class="contact-row">
        <div class="contact-person">
          <p class="contact-label">Contact</p>
          <p class="contact-name">Dale Whitacre</p>
          <p class="contact-line">
            <svg width="18" height="18" viewBox="0 0 24 24" aria-hidden="true">
              <circle cx="12" cy="12" r="10.5" fill="none" stroke="#fff" stroke-width="1.6"/>
              <path d="M9 7.5l1.6 2.4-1 1.2c.7 1.5 1.8 2.6 3.3 3.3l1.2-1 2.4 1.6-.8 1.6c-3.8-.3-7-3.5-7.3-7.3z" fill="#fff"/>
            </svg>
            610-555-0187
          </p>
        </div>
        <div class="address-block">
          <svg width="18" height="18" viewBox="0 0 24 24" aria-hidden="true">
            <circle cx="12" cy="12" r="10.5" fill="none" stroke="#fff" stroke-width="1.6"/>
            <path d="M12 5.5a4 4 0 0 0-4 4c0 3 4 8 4 8s4-5 4-8a4 4 0 0 0-4-4zm0 5.5a1.5 1.5 0 1 1 0-3 1.5 1.5 0 0 1 0 3z" fill="#fff"/>
          </svg>
          <p class="address">4076 Copper Ridge RD,<br>Larkfield, OH 43990</p>
        </div>
      </div>
      <div class="divider"></div>
      <p class="tagline">Committed to quality, service and integrity</p>
    </div>
  </section>
</main>
</body>
</html>
```